Local Flower Farm Needs Business Card Design

I need business cards designed for a flower farm based in Eudora, Kansas.
Business Info:
We are a local cut flower farm located in Eudora, Kansas, founded by Corinne Haldwick. What started as a passion for agriculture and search for more joy in daily life has blossomed into a small business dedicated to providing the community with beautiful, fresh, and sustainable flowers. We specialize in local, seasonal blooms, ensuring that every petal reflects the care and dedication we pour into our craft. Our mission is to deliver the highest quality flowers directly to our customers through local farmers markets and to florists who share our commitment to sustainability. Join us in celebrating the beauty of nature, one bloom at a time!
Contact Details:
Corinne Haldwick
Owner
Phone 913-555-0147
Facebook: Rosalind Thorpe Gardens
Instagram: @RosalindThorpeGardens
Website: RosalindThorpeGardens.example
Target Market(s)
Wholesale to Florists and Direct to Consumer via Farmers Market
Industry/Entity Type
Florist, Farm
Contact Information for Business Card
Name, Contact Info, Logo
Look and feel
Each slider illustrates characteristics of the customer's brand and the style your logo design should communicate.

```html
<!DOCTYPE html>
<html lang="en">
<head>
<meta charset="utf-8">
<title>Rosalind Thorpe Gardens – Business Card</title>
<link href="https://fonts.googleapis.com/css2?family=EB+Garamond:wght@400;600&display=swap" rel="stylesheet">
<style>
  :root {
    --ink: #0a272c;
    --paper: #ffffff;
    --shade: #c3c7ca;
    --stage: #e9eaeb;
    --card-w: 700px;
    --card-h: 400px;
  }
  * { box-sizing: border-box; margin: 0; padding: 0; }
  html, body {
    width: 1200px; height: 900px; overflow: hidden;
    background: var(--stage);
    font-family: "EB Garamond", Garamond, serif;
  }
  .stage {
    position: relative; width: 1200px; height: 900px;
    display: flex; flex-direction: column; align-items: center; justify-content: center; gap: 36px;
  }
  .card {
    position: relative; width: var(--card-w); height: var(--card-h);
    background: var(--ink); overflow: hidden;
    box-shadow: 0 6px 18px rgba(0,0,0,.18);
  }
  .brand-seal {
    position: absolute; width: 260px; height: 260px; border-radius: 50%;
    display: flex; align-items: center; justify-content: center; text-align: center;
    font-weight: 400; letter-spacing: .14em; text-transform: uppercase;
    font-size: 24px; line-height: 1.35;
  }
  .card--front .brand-seal {
    left: 220px; top: 70px; color: var(--paper); border: 1.5px solid var(--paper);
  }
  .card--back .curve { position: absolute; inset: 0; }
  .card--back .brand-seal {
    left: 420px; top: 28px; width: 230px; height: 230px; font-size: 21px;
    color: var(--ink); border: 1.5px solid var(--ink);
  }
  .contact {
    position: absolute; left: 54px; top: 190px; color: var(--paper);
  }
  .contact__name { font-weight: 600; font-size: 26px; line-height: 1.1; }
  .contact__role { font-size: 18px; margin-top: 2px; }
  .contact__list { list-style: none; margin-top: 26px; }
  .contact__list li {
    display: flex; align-items: center; gap: 8px; font-size: 19px; line-height: 1.3;
  }
  .contact__list svg { width: 15px; height: 15px; flex: none; }
  .dot-marker { width: 13px; height: 13px; border: 1.5px solid var(--paper); flex: none; border-radius: 2px; }
</style>
</head>
<body>
<main class="stage">
  <section class="card card--front" aria-label="Card front">
    <div class="brand-seal">Rosalind<br>Thorpe<br>Gardens</div>
  </section>

  <section class="card card--back" aria-label="Card back">
    <svg class="curve" viewBox="0 0 700 400" aria-hidden="true">
      <path d="M292 0 C320 190 500 316 700 300 L700 0 Z" fill="var(--shade)"/>
      <path d="M300 0 C330 180 510 296 700 282 L700 0 Z" fill="var(--paper)"/>
    </svg>
    <div class="brand-seal">Rosalind<br>Thorpe<br>Gardens</div>

    <div class="contact">
      <h1 class="contact__name">Corinne Haldwick</h1>
      <p class="contact__role">Owner</p>
      <ul class="contact__list">
        <li>
          <svg viewBox="0 0 16 16" aria-hidden="true"><path d="M2 6c0-2 2-3 6-3s6 1 6 3l-3 1-1-2H6L5 7zM4 8h8l1 5H3z" fill="#fff"/></svg>
          913-555-0147
        </li>
        <li>
          <svg viewBox="0 0 16 16" aria-hidden="true"><circle cx="8" cy="8" r="6.5" fill="none" stroke="#fff" stroke-width="1.4"/><ellipse cx="8" cy="8" rx="2.8" ry="6.5" fill="none" stroke="#fff" stroke-width="1.2"/><path d="M1.5 8h13" stroke="#fff" stroke-width="1.2"/></svg>
          RosalindThorpeGardens.example
        </li>
        <li><span class="dot-marker" aria-hidden="true"></span>Rosalind Thorpe Gardens</li>
        <li><span class="dot-marker" aria-hidden="true"></span>@RosalindThorpeGardens</li>
      </ul>
    </div>
  </section>
</main>
</body>
</html>
```